Veldmark Supplies Business Card

Professional business card that stand out to our potential customers. Front and back with clean modern design

Industry/Entity Type

Oil and gas

Contact Information for Business Card

Name, address, website , office phone and cell number

Requirements
Must have
• Editable files for each employee

```html
<!DOCTYPE html>
<html lang="en">
<head>
<meta charset="utf-8">
<title>Veldmark Supplies Business Card</title>
<link rel="stylesheet" href="https://fonts.googleapis.com/css2?family=Roboto:wght@400;500;700;900&display=swap">
<style>
  :root {
    --bg: #2b2b2d;
    --red: #e21e26;
    --blue: #2aa9cf;
    --white: #ffffff;
    --ink: #2a2a2a;
    --grad-blue: #27a8cc;
    --grad-red: #d9212c;
  }
  * { margin: 0; padding: 0; box-sizing: border-box; }
  html, body { width: 1200px; height: 852px; overflow: hidden; }
  body {
    background: var(--bg);
    font-family: "Roboto", Arial, sans-serif;
    position: relative;
  }
  .card {
    position: absolute;
    width: 500px;
    height: 286px;
    border-radius: 20px;
    overflow: hidden;
    top: 283px;
  }
  .card-back {
    left: 70px;
    background: linear-gradient(35deg, var(--grad-blue) 0%, #6b5d80 50%, var(--grad-red) 100%);
    display: flex;
    align-items: center;
    justify-content: center;
  }
  .brand {
    display: flex;
    align-items: center;
    gap: 10px;
    font-weight: 900;
    text-transform: uppercase;
    letter-spacing: 1px;
  }
  .brand-mark { width: 16px; height: 16px; }
  .card-back .brand { color: var(--white); font-size: 28px; }
  .card-back .brand-mark { background: var(--white); width: 20px; height: 20px; }

  .card-front { left: 630px; background: var(--white); }
  .front-waves { position: absolute; inset: 0; width: 500px; height: 286px; }
  .holder {
    position: absolute; right: 26px; top: 18px; text-align: right; color: var(--white);
  }
  .holder-name { font-size: 20px; font-weight: 700; }
  .holder-title { font-size: 11px; font-weight: 400; margin-top: 2px; }
  .contact {
    position: absolute; right: 22px; top: 138px; text-align: right;
    color: var(--ink); font-size: 11.5px; line-height: 16px;
  }
  .contact-row { display: flex; justify-content: flex-end; align-items: center; gap: 6px; }
  .contact-gap { height: 10px; }
  .icon { width: 11px; height: 11px; flex: none; }
  .icon-blank { width: 11px; }
  .card-front .brand {
    position: absolute; left: 30px; bottom: 32px; color: var(--red); font-size: 24px;
  }
  .card-front .brand-mark { background: var(--red); width: 18px; height: 18px; }
</style>
</head>
<body>
  <section class="card card-back" aria-label="Card back">
    <div class="brand"><span class="brand-mark"></span>Veldmark Supplies</div>
  </section>

  <section class="card card-front" aria-label="Card front">
    <svg class="front-waves" viewBox="0 0 500 286" aria-hidden="true">
      <path d="M0,0 H500 V58 C420,66 330,96 240,130 C150,164 70,172 0,182 Z" fill="var(--red)"/>
      <path d="M0,196 C80,184 160,172 250,138 C340,104 420,78 500,70" fill="none" stroke="var(--blue)" stroke-width="7"/>
      <path d="M20,206 C90,190 150,170 220,150" fill="none" stroke="var(--blue)" stroke-width="4"/>
    </svg>
    <div class="holder">
      <div class="holder-name">Jordan Hale</div>
      <div class="holder-title">Managing Director</div>
    </div>
    <div class="contact">
      <div class="contact-row">420 Larkspur Ave Suite 3
        <svg class="icon" viewBox="0 0 12 12"><path d="M6,0.5C3.8,0.5 2.2,2.1 2.2,4.2C2.2,7 6,11.5 6,11.5S9.8,7 9.8,4.2C9.8,2.1 8.2,0.5 6,0.5Z" fill="var(--red)"/><circle cx="6" cy="4.2" r="1.4" fill="var(--white)"/></svg>
      </div>
      <div class="contact-row">Midland Ridge, Tx 79000<span class="icon-blank"></span></div>
      <div class="contact-gap"></div>
      <div class="contact-row">(555)014-0287
        <svg class="icon" viewBox="0 0 12 12"><path d="M2.5,1 L4.5,1 L5.3,3.6 L4,4.6 C4.6,6 6,7.4 7.4,8 L8.4,6.7 L11,7.5 L11,9.5 C11,10.3 10.3,11 9.5,11 C5,11 1,7 1,2.5 C1,1.7 1.7,1 2.5,1Z" fill="var(--red)"/></svg>
      </div>
      <div class="contact-row">sales@veldmarksupplies.com
        <svg class="icon" viewBox="0 0 12 12"><rect x="0.5" y="2.5" width="11" height="7" fill="var(--red)"/><path d="M0.5,2.5 L6,6.5 L11.5,2.5" fill="none" stroke="var(--white)" stroke-width="1"/></svg>
      </div>
      <div class="contact-row">www.veldmarksupplies.com
        <svg class="icon" viewBox="0 0 12 12"><circle cx="6" cy="6" r="5.5" fill="var(--red)"/><path d="M0.5,6 H11.5 M6,0.5 C3.5,3 3.5,9 6,11.5 M6,0.5 C8.5,3 8.5,9 6,11.5" fill="none" stroke="var(--white)" stroke-width="0.8"/></svg>
      </div>
    </div>
    <div class="brand"><span class="brand-mark"></span>Veldmark Supplies</div>
  </section>
</body>
</html>
```